We need a business card design, letterhead design and envelope design for our corporate image

We are looking for a corporate business card design, letterhead and envelope design to match the business card design. Logo is done.

```html
<!DOCTYPE html>
<html lang="en">
<head>
<meta charset="utf-8">
<title>Vantora Business Card</title>
<link rel="stylesheet" href="https://fonts.googleapis.com/css2?family=Oswald:wght@600&family=Montserrat:wght@300;400;500&display=swap">
<style>
  :root {
    --page-bg: #2a2a2d;
    --card-bg: #1f1f20;
    --accent: #f5c400;
    --text-light: #f2f2f2;
    --brand-grey: #8a8a8c;
  }
  * { margin: 0; padding: 0; box-sizing: border-box; }
  html, body { width: 1200px; height: 786px; overflow: hidden; }
  body {
    background: var(--page-bg);
    display: flex;
    align-items: center;
    justify-content: center;
    gap: 40px;
    font-family: "Montserrat", sans-serif;
  }
  .card {
    width: 560px;
    height: 320px;
    background: var(--card-bg);
    border: 7px solid var(--accent);
    position: relative;
    box-shadow: 0 14px 30px rgba(0,0,0,0.45);
  }
  .card-front {
    display: flex;
    align-items: center;
    justify-content: center;
    gap: 26px;
    padding-left: 40px;
  }
  .identity { text-align: right; }
  .identity .name {
    font-family: "Oswald", sans-serif;
    font-weight: 600;
    font-size: 36px;
    line-height: 1;
    letter-spacing: 0.5px;
    color: var(--accent);
    text-transform: uppercase;
  }
  .identity .role {
    font-weight: 300;
    font-size: 15px;
    letter-spacing: 1px;
    color: var(--text-light);
    text-transform: uppercase;
    margin-top: 2px;
  }
  .divider {
    width: 1.5px;
    height: 86px;
    background: var(--accent);
  }
  .contact-list { list-style: none; }
  .contact-list li {
    display: flex;
    align-items: center;
    gap: 9px;
    font-size: 13.5px;
    font-weight: 400;
    color: var(--text-light);
    line-height: 1.5;
  }
  .contact-list svg {
    width: 11px;
    height: 11px;
    flex: none;
    fill: none;
    stroke: var(--accent);
    stroke-width: 2;
  }
  .contact-list svg .solid { fill: var(--accent); stroke: none; }
  .card-back {
    display: flex;
    align-items: center;
    justify-content: center;
  }
  .brand-name {
    font-family: "Montserrat", sans-serif;
    font-weight: 500;
    font-size: 54px;
    letter-spacing: 1px;
    color: var(--brand-grey);
  }
</style>
</head>
<body>
  <section class="card card-front">
    <div class="identity">
      <p class="name">Daniel Brooks</p>
      <p class="role">Director</p>
    </div>
    <div class="divider"></div>
    <ul class="contact-list">
      <li>
        <svg viewBox="0 0 12 12" aria-hidden="true"><path class="solid" d="M2.5 0.8 L4.5 0.5 L5.3 3.2 L4 4.2 Q5.2 6.8 7.8 8 L8.8 6.7 L11.5 7.5 L11.2 9.5 Q10.5 11.5 8.5 11.2 Q1.5 9.8 0.8 3.5 Q0.6 1.3 2.5 0.8 Z"/></svg>
        +330 5172-4036
      </li>
      <li>
        <svg viewBox="0 0 12 12" aria-hidden="true"><rect x="1" y="2.5" width="10" height="7" rx="0.8"/><path d="M1.3 3 L6 6.6 L10.7 3"/></svg>
        hello@vantora.com
      </li>
      <li>
        <svg viewBox="0 0 12 12" aria-hidden="true"><circle cx="6" cy="6" r="5"/><ellipse cx="6" cy="6" rx="2.2" ry="5"/><path d="M1 6 H11"/></svg>
        www.vantora.com
      </li>
      <li>
        <svg viewBox="0 0 12 12" aria-hidden="true"><path class="solid" d="M6 0.5 A4 4 0 0 1 10 4.5 Q10 7.5 6 11.5 Q2 7.5 2 4.5 A4 4 0 0 1 6 0.5 Z M6 3 A1.5 1.5 0 1 0 6 6 A1.5 1.5 0 1 0 6 3 Z"/></svg>
        Dayton, OH USA
      </li>
    </ul>
  </section>

  <section class="card card-back">
    <span class="brand-name">Vantora</span>
  </section>
</body>
</html>
```